Stationery Design Project

Our company is "Meridian Systems" and we have a product called "lunogrid.com". The product is an online accounting software for businesses. We want to communicate that our software will help business owners to be more efficient and help them track their finances better. Lunogrid.com is basically a simple version of ledgerpal.

"We want a unique and creative design which will surprise our customer."

NAME CARD = LUNOGRID
We want a lunogrid name card NOT MERIDIAN SYSTEMS.

For the content of the name card, please make sure it fit with a long name like the following:

Rudi Wahyo Alias Rudi
Developer Specialist
T: (021) 4827 1036
F: (021) 4827 1037
E: customer.service@mrdn-sys.example

I need you to put it the following information to the name card

"lunogrid"
- moto is "automate your businesses"
- website "www.lunogrid.com"
- lunogrid is a "Web Accounting Software"
- product of "Meridian Systems"

LETTERHEAD, ENVELOPE, FOLDER = MERIDIAN SYSTEMS
Other than name card we wanted you to design for us; letterhead, envelope and folder. In letterhead, envelope and folder it should ONLY contain the following information ("Meridian Systems").
PLEASE BE SURE YOU ARE NOT PUTTING "LUNOGRID LOGO" IN LETTERHEAD, ENVELOPE AND FOLDER.

"Meridian Systems"
Address:
Ruko Graha Pelangi Blok. D No. 18
Jl. Kenanga Raya No. 71
Jakarta
Cempaka, 11470
Indonesia

Web Address: mrdn-sys.example

T: (021) 4827 1036
F: (021) 4827 1037

Target Market(s)

Business Owners, Accountant, Auditor, Tax Consultant

Industry/Entity Type

Accounting

Requirements

```html
<!DOCTYPE html>
<html lang="en">
<head>
<meta charset="utf-8">
<title>Lunogrid Name Card</title>
<link rel="stylesheet" href="https://fonts.googleapis.com/css2?family=Alegreya+Sans:wght@400;500;700&family=Alegreya+Sans+SC:wght@400;500&display=swap">
<style>
  :root {
    --canvas: #ffffff;
    --card-edge: #8a8a8a;
    --lime: #c4ff00;
    --leaf: #4fb800;
    --forest: #1a3209;
    --ink: #3f4a4f;
    --product-ink: #1c1c1c;
    --charcoal: #505050;
    --white: #ffffff;
  }
  * { margin: 0; padding: 0; box-sizing: border-box; }
  html, body {
    width: 1200px; height: 900px; overflow: hidden;
    background: var(--canvas);
    font-family: "Alegreya Sans", sans-serif;
  }
  .canvas { position: relative; width: 1200px; height: 900px; }

  /* Front of card */
  .card-front {
    position: absolute; left: 159px; top: 197px;
    width: 379px; height: 433px;
    border: 1px solid var(--card-edge);
    background: var(--white);
  }
  .accent-strip {
    position: absolute; left: 0; top: 0; width: 44px; height: 100%;
    background: linear-gradient(to bottom,
      var(--lime) 0%, var(--leaf) 25%, var(--forest) 50%,
      var(--leaf) 75%, var(--lime) 100%);
  }
  .fold-line {
    position: absolute; left: 44px; right: 0; top: 215px;
    border-top: 1px solid var(--card-edge);
  }
  .panel {
    position: absolute; left: 44px; right: 0; height: 216px;
    text-align: center; color: var(--ink);
  }
  .panel-product { top: 0; transform: rotate(180deg); }
  .panel-category { top: 216px; }

  .product-name {
    position: absolute; left: 0; right: 0; top: 62px;
    font-size: 28px; font-weight: 700; color: var(--product-ink); letter-spacing: 0.5px;
  }
  .product-name .mark-square {
    display: inline-block; width: 14px; height: 14px; background: var(--product-ink);
    margin-right: 9px; vertical-align: 2px;
  }
  .product-motto {
    position: absolute; left: 0; right: 0; top: 146px;
    font-family: "Alegreya Sans SC", sans-serif;
    font-size: 16px; letter-spacing: 1.5px;
  }
  .product-site {
    position: absolute; left: 0; right: 0; top: 182px;
    font-size: 15px; letter-spacing: 0.3px;
  }

  .product-category {
    position: absolute; left: 0; right: 0; top: 72px;
    font-size: 21px; font-weight: 500; color: var(--ink); letter-spacing: 0.8px;
  }
  .product-maker {
    position: absolute; left: 0; right: 0; top: 139px;
    font-family: "Alegreya Sans SC", sans-serif;
    font-size: 14px; letter-spacing: 3px;
  }

  /* Back of card */
  .card-back {
    position: absolute; left: 661px; top: 193px;
    width: 379px; height: 433px;
  }
  .back-header {
    position: absolute; left: 0; top: 0; width: 100%; height: 217px;
    background: linear-gradient(to bottom, #17300a 0%, #3f8e04 40%, var(--leaf) 62%, var(--lime) 100%);
  }
  .back-site {
    position: absolute; left: 0; right: 0; top: 94px;
    text-align: center; color: var(--white); font-size: 19px; letter-spacing: 0.5px;
  }
  .back-contact {
    position: absolute; left: 0; top: 217px; width: 100%; height: 216px;
    background: var(--charcoal); color: var(--white);
    padding: 48px 0 0 95px;
  }
  .holder-name {
    font-family: "Alegreya Sans SC", sans-serif;
    font-weight: 400;
    font-size: 19px; letter-spacing: 0.8px; margin-bottom: 12px;
  }
  .holder-details { list-style: none; font-size: 16.5px; line-height: 18px; }
</style>
</head>
<body>
<main class="canvas">
  <section class="card-front">
    <div class="accent-strip"></div>
    <div class="fold-line"></div>

    <div class="panel panel-product">
      <div class="product-name"><span class="mark-square"></span>lunogrid</div>
      <div class="product-motto">Automate Your Businesses</div>
      <div class="product-site">www.lunogrid.com</div>
    </div>

    <div class="panel panel-category">
      <div class="product-category">Web Accounting Software</div>
      <div class="product-maker">a product of Meridian Systems</div>
    </div>
  </section>

  <section class="card-back">
    <div class="back-header">
      <div class="back-site">mrdn-sys.example</div>
    </div>
    <div class="back-contact">
      <h1 class="holder-name">Rudi Wahyo Alias Rudi</h1>
      <ul class="holder-details">
        <li>Developer Specialist</li>
        <li>T: (021) 4827 1036</li>
        <li>F: (021) 4827 1037</li>
        <li>E: customer.service@mrdn-sys.example</li>
      </ul>
    </div>
  </section>
</main>
</body>
</html>
```